Chorefinch clone for Asia

I am developing a clone for www.chorefinchly.example. It is meant for Asia (i.e. Singapore, Australia, Indonesian, Philippines, Malaysia).

I need a webdesign that functionally look like chorefinch, but localised with pictures of Asian of multi country (rather than latin american looks).

The color, iconography, images can be different, but the functionality must be all be similar to www.chorefinchly.example

I need a mobile UI as well that is for a mobile app, again, similar to that of chorefinch mobile app.

Note that I need the design for the following pages:
1. homepage
2. login page
3. page after login in.
4. search page & results
5. post a task & confirmation page
6. Payment page
7. User Review page.
8. Sign up page.

The webpages are to be in english....

The features must have photos of friendly looking helpers.

Target Market(s)

Asian countries. To serve a mass market, for part time, one off task job.

Requirements
Must have
• Just use ChoreFinchAsia for the name of the site for Starters. I have not arrived at a name yet.

```html
<!DOCTYPE html>
<html lang="en">
<head>
<meta charset="utf-8">
<title>Post a Task – Mei Lan</title>
<link rel="stylesheet" href="https://fonts.googleapis.com/css2?family=Cabin:ital,wght@0,400;0,500;0,600;1,400&display=swap">
<style>
:root{
  --teal:#3f9ea0;
  --teal-dark:#2f8487;
  --teal-light:#7cc2c3;
  --header-bg:#d3e4e6;
  --panel:#e9eff1;
  --field:#eef3f4;
  --orange:#f29a0e;
  --orange-dark:#d97c00;
  --maroon:#7a1f1f;
  --gold:#d7890c;
  --ink:#4a4a4a;
  --muted:#8a8a8a;
  --blue:#3f8fc0;
  --grey-bar:#a9adb0;
  --footer:#dfe9eb;
  --footer-bottom:#c9dcdf;
  --link:#2d6f9c;
}
*{box-sizing:border-box;margin:0;padding:0}
html,body{width:969px;height:1200px;overflow:hidden}
body{position:relative;background:#fff;font-family:"Cabin",sans-serif;color:var(--ink);font-size:12px}
.abs{position:absolute}
ul{list-style:none}

/* header */
.site-header{position:absolute;left:0;top:0;width:969px;height:126px;background:linear-gradient(#d9e8ea,#cde0e3);border-bottom:1px solid #b9d0d3}
.top-strip{position:absolute;left:0;top:0;width:969px;height:12px;background:var(--teal)}
.main-nav{position:absolute;left:511px;top:0;width:419px;height:48px;background:linear-gradient(#45a4a6,#2f8a8d);border-radius:0 0 8px 14px;display:flex;align-items:center}
.main-nav a{color:#fff;text-decoration:none;font-size:14px;padding:0 14px;height:48px;line-height:50px;border-right:1px solid rgba(0,0,0,.15)}
.main-nav a:last-child{border-right:0}
.main-nav a.active{background:linear-gradient(#6bbcbd,#4aa3a5);border-radius:0 0 0 12px;padding:0 20px}
.brand{position:absolute;left:40px;top:52px;display:flex;align-items:center;gap:12px}
.brand-dot{width:44px;height:44px;border-radius:50%;background:var(--orange)}
.brand-name{font-size:46px;font-weight:500;color:var(--teal);line-height:1}
.social{position:absolute;top:71px;height:25px;border-radius:3px;background:linear-gradient(#4a9fd8,#2b7fbf);color:#fff;font-size:10px;display:flex;align-items:center;padding-left:30px;border:1px solid #246fa6}
.social::before{content:"";position:absolute;left:0;top:0;width:24px;height:100%;border-right:1px solid rgba(255,255,255,.4)}
.social.chirp{left:512px;width:121px}
.social.face{left:648px;width:129px;background:linear-gradient(#5575b0,#3b5a96);border-color:#2f4b80}
.search{position:absolute;left:792px;top:71px;width:136px;height:24px;background:#fff;border:1px solid #b9cccf;border-radius:2px;font-size:10px;font-style:italic;color:#999;padding:5px 12px}
.search svg{position:absolute;right:6px;top:6px}

/* steps panel */
.steps-panel{position:absolute;left:40px;top:130px;width:890px;height:113px;background:linear-gradient(#f3f7f8,#e3ecee);border-radius:0 0 10px 10px}
.steps-panel h1{position:absolute;left:22px;top:14px;font-size:21px;font-weight:400;color:var(--maroon)}
.step{position:absolute;top:52px;width:100px;text-align:center}
.step b{display:block;height:29px;line-height:29px;font-weight:400;font-size:15px;color:#fff;background:linear-gradient(#b3b7ba,#999ea2);border-radius:2px}
.step.on b{background:linear-gradient(#ffa81b,#ef8d00);border-radius:14px 2px 2px 14px}
.step.last b{border-radius:2px 14px 14px 2px}
.step span{display:block;margin-top:6px;color:#a5a5a5;font-size:14px}
.steps-divider{position:absolute;left:551px;top:20px;width:1px;height:78px;background:#c9d3d5}
.deadline-label{position:absolute;left:599px;top:21px;font-size:13px;font-weight:600;color:#555}
.deadline-text{position:absolute;left:650px;top:53px;font-size:12px;color:#555;line-height:19px}
.deadline-text strong{color:var(--orange-dark);font-weight:600;font-size:13px}
.btn{display:inline-block;color:#fff;text-align:center;background:linear-gradient(#ffb021,#ee8a00);border:1px solid #d47a00;border-radius:3px;box-shadow:0 3px 0 #e4c79a;font-size:13px}
.deadline-change{position:absolute;left:801px;top:56px;width:71px;height:30px;line-height:28px}

/* form */
.page-title{position:absolute;left:63px;top:265px;font-size:19px;font-weight:400;color:var(--gold)}
.field-label{position:absolute;left:64px;font-size:14px;color:var(--gold)}
.field-label em{color:#c0392b;font-style:normal}
.field{position:absolute;left:63px;width:526px;background:var(--field);border-radius:4px;color:#555;font-size:12.5px}
.title-field{top:352px;height:45px;padding:14px 14px}
.desc-field{top:455px;height:97px;padding:17px 16px;line-height:20.5px;text-align:justify}
.private-notes{position:absolute;left:497px;top:431px;font-size:10.5px;font-style:italic;color:var(--muted)}
.option{position:absolute;top:585px;display:flex;gap:10px}
.option h3{font-size:13px;font-weight:400;color:var(--teal-dark)}
.option p{font-size:10.5px;font-style:italic;color:var(--muted);margin-top:4px}
.pay-question{position:absolute;left:64px;top:662px;font-size:14px;color:var(--gold)}
.pay-box{position:absolute;left:63px;top:690px;width:526px;height:97px;background:var(--field);border-radius:4px}
.price-input{position:absolute;left:118px;top:17px;width:138px;height:31px;background:#fff;border:1px solid #c4d0d2;font-size:17px;color:#999;padding:4px 14px}
.price-avg{position:absolute;left:264px;top:24px;font-size:12.5px;color:#555}
.price-avg strong{color:var(--teal-dark);font-size:15px}
.price-note{position:absolute;left:118px;top:65px;font-size:10.5px;font-style:italic;color:var(--muted)}
.save-btn{position:absolute;left:415px;top:816px;width:173px;height:40px;line-height:38px;font-size:17px;letter-spacing:.3px;border-radius:4px}

/* sidebar */
.card{position:absolute;left:639px;width:272px;background:var(--panel);border-radius:8px;overflow:hidden}
.card h2{height:39px;line-height:40px;padding-left:18px;font-size:17px;font-weight:400;color:#fff;background:linear-gradient(#6ab6b8,#4ba2a5);border-bottom:3px solid #fff}
.summary{top:260px;height:173px}
.summary .task{margin:14px 18px 0 27px;color:var(--gold);font-size:14px;line-height:19px}
.summary .repeat{margin:8px 0 0 27px;font-size:10.5px;color:#555}
.summary .btn{position:absolute;left:28px;top:128px;width:69px;height:30px;line-height:28px}
.pricing{top:444px;height:329px}
.pricing .basis{text-align:center;font-size:12px;font-weight:600;color:#555;margin:12px 16px 0;padding-bottom:8px;border-bottom:1px solid #d3dcde}
.bars{margin:16px 0 0 17px}
.bars li{display:flex;align-items:center;height:38px}
.bars b{width:39px;font-size:17px;font-weight:600;color:var(--blue)}
.bar{width:199px;height:7px;background:var(--grey-bar);border-radius:4px;overflow:hidden}
.bar i{display:block;height:100%;background:var(--orange)}

/* cities */
.city-rule{position:absolute;left:40px;top:895px;width:890px;height:1px;background:#d5dadb}
.cities{position:absolute;top:909px;width:220px}
.cities h4{font-size:14.5px;font-weight:400;color:#333;margin-bottom:8px}
.cities li{font-size:12px;color:#555;height:21px;padding-left:12px;position:relative}
.cities li::before{content:"→";position:absolute;left:0;top:0;font-size:9px;color:#777}

/* footer */
.site-footer{position:absolute;left:0;top:1031px;width:969px;height:108px;background:var(--footer)}
.foot-col{position:absolute;top:15px}
.foot-col h5{font-size:12px;font-weight:400;color:var(--link);margin-bottom:10px;height:14px}
.foot-col li{font-size:11px;color:#555;height:20.5px;padding-left:11px;position:relative}
.foot-col li::before{content:"";position:absolute;left:1px;top:4px;border:3px solid transparent;border-left:4px solid #555}
.pay-marks{display:flex;gap:5px;margin-top:10px}
.pay-marks span{width:27px;height:18px;border-radius:2px;background:#fff;border:1px solid #b9c6c9}
.pay-marks span:nth-child(2){background:#cfd9e6}
.pay-marks span:nth-child(3){background:#f2c7a4}
.pay-marks span:nth-child(5){background:#c8d3ea}
.call{font-size:12px;color:var(--link);margin-top:16px}
.bottom-bar{position:absolute;left:0;top:1139px;width:969px;height:61px;background:var(--footer-bottom)}
.bottom-links{position:absolute;left:52px;top:19px;font-size:11px;color:#444}
.bottom-links span{margin:0 6px;color:#666}
.copyright{position:absolute;right:35px;top:19px;font-size:11px;color:#444}
</style>
</head>
<body>

<header class="site-header">
  <div class="top-strip"></div>
  <nav class="main-nav">
    <a class="active">Home</a><a>Who we are</a><a>How it works</a><a>Sign up</a><a>Login</a>
  </nav>
  <div class="brand"><span class="brand-dot"></span><span class="brand-name">Mei Lan</span></div>
  <div class="social chirp">Sign in with Chirpline</div>
  <div class="social face">Sign in with Facepage</div>
  <div class="search">Search
    <svg width="11" height="11" viewBox="0 0 11 11"><circle cx="4.5" cy="4.5" r="3.3" fill="none" stroke="#aaa" stroke-width="1.4"/><line x1="7" y1="7" x2="10" y2="10" stroke="#aaa" stroke-width="1.6"/></svg>
  </div>
</header>

<section class="steps-panel">
  <h1>Post a Task</h1>
  <div class="step on" style="left:24px"><b>Describe</b><span>Step 1</span></div>
  <div class="step" style="left:147px"><b>Sign up</b><span>Step 2</span></div>
  <div class="step" style="left:272px"><b>Review</b><span>Step 3</span></div>
  <div class="step last" style="left:395px"><b>Done</b><span>Step 4</span></div>
  <div class="steps-divider"></div>
  <div class="deadline-label">Deadline:</div>
  <svg class="abs" style="left:604px;top:55px" width="32" height="36" viewBox="0 0 32 36">
    <rect x="1" y="3" width="30" height="32" rx="2" fill="#fff" stroke="#ccc"/>
    <rect x="1" y="3" width="30" height="9" rx="2" fill="#5fb04a"/>
    <text x="16" y="31" text-anchor="middle" font-family="Cabin,sans-serif" font-size="17" font-weight="600" fill="#222">7</text>
  </svg>
  <div class="deadline-text">I need this task done by<br><strong>Monday at 11:00 AM</strong></div>
  <span class="btn deadline-change">CHANGE</span>
</section>

<main>
  <h2 class="page-title">Post a Task</h2>

  <label class="field-label" style="top:324px">Task Title <em>*</em></label>
  <div class="field title-field">At vero eos et accusamus et iusto odio dignissimos ducimus qui blanditiis praesentium</div>

  <label class="field-label" style="top:427px">Task Description <em>*</em></label>
  <span class="private-notes">Add Private Notes</span>
  <div class="field desc-field">Temporibus autem quibusdam et aut officiis debitis aut rerum necessitatibus saepe eveniet ut et voluptates repudiandae sint et molestiae non recusandae. Itaque earum rerum hic tenetur a sapiente delectus.</div>

  <div class="option" style="left:63px">
    <svg width="32" height="38" viewBox="0 0 32 38"><path d="M16 2a12 12 0 0 0-12 12c0 9 12 22 12 22s12-13 12-22A12 12 0 0 0 16 2z" fill="#e6e9ea" stroke="#b9bec0" stroke-width="1.5"/><circle cx="16" cy="14" r="4.5" fill="#fff" stroke="#b9bec0"/></svg>
    <div><h3>Add another location</h3><p>Officia deserunt mollitia animi</p></div>
  </div>
  <div class="option" style="left:321px">
    <svg width="32" height="38" viewBox="0 0 32 38"><ellipse cx="16" cy="19" rx="13" ry="16" fill="#f3c316" stroke="#d59d00" stroke-width="1.5"/><rect x="13" y="10" width="6" height="18" rx="2" fill="#e3a800"/></svg>
    <div><h3>Need to Spend Money</h3><p>No one rejects, dislikes, or avoids pleasure itself</p></div>
  </div>

  <p class="pay-question">How much are you willing to pay for this Task?</p>
  <div class="pay-box">
    <svg class="abs" style="left:33px;top:32px" width="53" height="36" viewBox="0 0 53 36"><rect x="1" y="1" width="51" height="34" rx="3" fill="#7fa9d6" stroke="#3e6a9a"/><rect x="1" y="7" width="51" height="6" fill="#2f4f72"/><rect x="6" y="18" width="38" height="8" fill="#eef3f8"/></svg>
    <div class="price-input">$</div>
    <p class="price-avg"><strong>$59</strong> is the average price for similar Tasks</p>
    <p class="price-note">Your price is private and helps us determine when ChoreFinches make good offers</p>
  </div>

  <span class="btn save-btn">SAVE &amp; CONTINUE</span>
</main>

<aside>
  <section class="card summary">
    <h2>Your task so far:</h2>
    <p class="task">A little baking and then a trip to the post office to mail your creation</p>
    <p class="repeat">This Task does not repeat</p>
    <span class="btn">CHANGE</span>
  </section>
  <section class="card pricing">
    <h2>TaskPrice for Tasks of this type</h2>
    <p class="basis">Based on Historical Data</p>
    <ul class="bars">
      <li><b>$10</b><span class="bar"><i style="width:27%"></i></span></li>
      <li><b>$30</b><span class="bar"><i style="width:63%"></i></span></li>
      <li><b>$45</b><span class="bar"><i style="width:37%"></i></span></li>
      <li><b>$60</b><span class="bar"><i style="width:31%"></i></span></li>
      <li><b>$80</b><span class="bar"><i style="width:27%"></i></span></li>
      <li><b>$95</b><span class="bar"><i style="width:27%"></i></span></li>
    </ul>
  </section>
</aside>

<div class="city-rule"></div>
<div class="cities" style="left:64px"><h4>Popular Cities in Australia</h4><ul><li>Melbourne</li><li>Sydney</li><li>Adelaide</li><li>Berth</li></ul></div>
<div class="cities" style="left:291px"><h4>Popular Cities in Singapore</h4><ul><li>Aljunied</li><li>Bencoolen</li><li>Dunearn</li><li>Ayer Rajah</li></ul></div>
<div class="cities" style="left:518px"><h4>Popular Cities in Malaysia</h4><ul><li>George Town</li><li>Kuala Lumpur</li><li>Ipoh</li><li>Kuching</li></ul></div>
<div class="cities" style="left:745px"><h4>Popular Cities in Philipines</h4><ul><li>Abra</li><li>Agusan del Sur</li><li>Basilan</li><li>Cagayan</li></ul></div>

<footer class="site-footer">
  <div class="foot-col" style="left:51px"><h5>About us</h5><ul><li>Praesent tempor</li><li>Cras vel</li><li>Etiam porttitor</li></ul></div>
  <div class="foot-col" style="left:183px"><h5></h5><ul><li>Praesent tempor</li><li>Cras vel</li><li>Etiam porttitor</li></ul></div>
  <div class="foot-col" style="left:315px"><h5>Credit Details</h5><ul><li>Praesent tempor</li><li>Cras vel</li><li>Etiam porttitor</li></ul></div>
  <div class="foot-col" style="left:448px"><h5>Popular Cities</h5><ul><li>Praesent tempor</li><li>Cras vel</li><li>Etiam porttitor</li></ul></div>
  <div class="foot-col" style="left:580px"><h5>Customer Support</h5><ul><li>Praesent tempor</li><li>Cras vel</li><li>Etiam porttitor</li></ul></div>
  <div class="foot-col" style="left:729px"><h5>Payments</h5>
    <div class="pay-marks"><span></span><span></span><span></span><span></span><span></span></div>
    <p class="call">Call us : 555 010 2468</p>
  </div>
</footer>
<div class="bottom-bar">
  <p class="bottom-links">Home<span>|</span>Who we are<span>|</span>How it works<span>|</span>Sign up<span>|</span>Log in<span>|</span>FAQ<span>|</span>Support<span>|</span>Privacy Policy<span>|</span>Terms and Conditions</p>
  <p class="copyright">Copyright © 2012 Mei Lan. &nbsp;&nbsp;All rights reserved.</p>
</div>

</body>
</html>
```